Simple and Clean business card design

We would like the design to be simple clean and to incorporate our colors.

We are open to your design and talent, we have the dots in our logo as we think of it as data points and we connect data points for people.

We are open to see the great creative and clean design you bring to the table

Contact Information for Business Card

please include: name, position, email, phone and website

Font styles to use
Sans Serif

Requirements
Must have
• my colors incorporated, simplicity
Nice to have
• lots of white space, simplicity
Should not have
• complexicity/ complex art

```html
<!DOCTYPE html>
<html lang="en">
<head>
<meta charset="utf-8">
<title>Quarry — Business Card</title>
<link rel="stylesheet" href="https://fonts.googleapis.com/css2?family=Montserrat:wght@400;500;700&display=swap">
<style>
  :root {
    --stage: #e9e9eb;
    --card-white: #ffffff;
    --card-dark: #1b1c1e;
    --pattern-light: #4a4b4e;
    --pattern-dark: #232426;
    --ink: #111111;
    --muted: #7a7a7a;
    --rule: #9a9a9a;
    --blue: #4f7cc6;
    --green: #34a853;
    --yellow: #f5bd17;
    --red: #e53b2c;
  }
  * { box-sizing: border-box; margin: 0; padding: 0; }
  html, body {
    width: 1200px; height: 900px; overflow: hidden;
    background: var(--stage);
    font-family: "Montserrat", sans-serif;
  }
  .stage {
    width: 1200px; height: 900px;
    display: flex; flex-direction: column;
    align-items: center; justify-content: center; gap: 56px;
  }
  .card {
    width: 600px; height: 343px;
    position: relative; overflow: hidden;
    box-shadow: 0 10px 28px rgba(0,0,0,0.18);
  }
  /* Back */
  .card-back { background: var(--card-dark); }
  .back-pattern {
    position: absolute; inset: 0;
    background: linear-gradient(110deg, var(--pattern-light) 0%, var(--pattern-dark) 70%, var(--card-dark) 100%);
    opacity: 0.55;
  }
  .back-mark {
    position: absolute; left: 470px; top: 182px;
    width: 26px; height: 26px; border-radius: 50%;
    background: var(--blue);
  }
  /* Front */
  .card-front { background: var(--card-white); }
  .brand {
    position: absolute; left: 46px; top: 140px;
    display: flex; align-items: center; gap: 10px;
  }
  .brand-dot { width: 30px; height: 30px; border-radius: 50%; background: var(--blue); }
  .brand-name {
    font-weight: 700; font-size: 54px; letter-spacing: -1px;
    color: var(--ink); line-height: 1;
  }
  .divider {
    position: absolute; left: 316px; top: 64px;
    width: 1px; height: 216px; background: var(--rule);
  }
  .details { position: absolute; left: 336px; top: 62px; }
  .person-name {
    font-weight: 700; font-size: 20px; color: var(--ink);
    text-transform: uppercase; letter-spacing: 0.5px;
  }
  .person-role { font-size: 17px; color: var(--muted); margin-top: 4px; }
  .address { font-size: 12.5px; color: var(--muted); margin-top: 18px; line-height: 1.4; letter-spacing: 0.3px; }
  .contacts { list-style: none; margin-top: 16px; }
  .contacts li {
    display: flex; align-items: center; gap: 10px;
    font-size: 13px; color: var(--muted); letter-spacing: 0.4px;
    margin-bottom: 6px;
  }
  .contacts svg { width: 13px; height: 13px; flex: none; }
</style>
</head>
<body>
<main class="stage">
  <section class="card card-back" aria-label="Card back">
    <div class="back-pattern" role="img" aria-label="Pattern of scattered grey dots fading across the dark card"></div>
    <div class="back-mark"></div>
  </section>

  <section class="card card-front" aria-label="Card front">
    <div class="brand">
      <span class="brand-dot"></span>
      <span class="brand-name">quarry</span>
    </div>
    <div class="divider"></div>
    <div class="details">
      <p class="person-name">Marcus Ellery</p>
      <p class="person-role">Founder/ CEO</p>
      <p class="address">18 W. Orchard Lane<br>Brookfield, IL 60513</p>
      <ul class="contacts">
        <li>
          <svg viewBox="0 0 16 16" aria-hidden="true"><path fill="var(--green)" d="M3.5 1.5l2.5 0 1 3.5-1.6 1.2a8 8 0 0 0 4.4 4.4L11 9l3.5 1v2.5c0 1-1 2-2 2A11 11 0 0 1 1.5 3.5c0-1 1-2 2-2z"/></svg>
          555-214-0387
        </li>
        <li>
          <svg viewBox="0 0 16 16" aria-hidden="true"><rect x="1" y="3" width="14" height="10" fill="var(--yellow)"/><path d="M1 3l7 6 7-6" fill="none" stroke="#fff" stroke-width="1.3"/></svg>
          marcus.ellery@quarry.one
        </li>
        <li>
          <svg viewBox="0 0 16 16" aria-hidden="true"><circle cx="8" cy="8" r="7" fill="var(--red)"/><path d="M1 8h14M8 1c-3 3.5-3 10.5 0 14M8 1c3 3.5 3 10.5 0 14" fill="none" stroke="#fff" stroke-width="1"/></svg>
          www.quarry.one
        </li>
      </ul>
    </div>
  </section>
</main>
</body>
</html>
```